Tidy4all

Full service cleaning company. Specializing in commercial and apartment cleans.
Fully licensed and insured
Digital photos and invoices provided
for every job
For web designer...basic info as expected by a highend cleaning company that provides excellent service at reasonable pricing. We are going after large property management companies as well as not pricing ourselves out to help the local mom and pop companies as well.
Updates

Project Deadline Extended Reason: Everyone seems to be having trouble understanding that we are a dumpster company that is adding a cleaning side to the company. We want our clients to see Tidy4All as a separate branch of our our already established waste management company.We are not a regular cleaning company. We specialize in going after large commercial cleans and apartment cleans. I have now included info regarding a proposal for work and our invoice/job completion to make it clearer what we do Added Monday, July 20, 2015

Target Market(s)

Property Management companies in Savannah, Richmond Hill, Rincon, Hinesville and Midway Georgia

Industry/Entity Type

Cleaning Service

Coding

Coded - Design and coding required

Number of Pages Required

3 page

Requirements
Must have
• Nice home page with lots of photos (stock are fine) to convey exactly what we do (getting logo bid on right now on this sight).
• Information page with employee photos (can leave blank) need room for 4 photos and bios.
• Page or link to a static page for the dumpster company BinRun (logo for this is red and black file attached along with photo of dumpster. This page just needs to be one page with contact info and information about commercial dumpster.
• Basically this site is just a fluff page used for marketing purposes. Its content can be general and once created wont change much. Services and photos can be provided upon request but general layout and info is what we are looking for.

```html
<!DOCTYPE html>
<html lang="en">
<head>
<meta charset="utf-8">
<title>Tidy4All – Full Service Cleaning</title>
<link rel="stylesheet" href="https://fonts.googleapis.com/css2?family=Open+Sans:wght@400;600;700&family=PT+Serif:wght@400;700&display=swap">
<style>
  :root{
    --red:#e32421;
    --red-dark:#b81512;
    --ink:#1b1b1b;
    --text:#555;
    --muted:#8a8a8a;
    --paper:#ffffff;
    --band:#ececec;
    --line:#d9d9d9;
    --green:#8fbc1f;
    --footer:#151515;
    --footer-text:#a9a9a9;
  }
  *{box-sizing:border-box;margin:0;padding:0}
  html,body{width:681px;height:1200px;overflow:hidden;background:var(--paper)}
  body{font-family:"Open Sans",Arial,sans-serif;color:var(--text);position:relative}
  .serif{font-family:"PT Serif",Georgia,serif}

  /* header */
  .site-header{position:absolute;left:0;top:0;width:681px;height:64px}
  .brand{position:absolute;left:50px;top:16px;display:flex;align-items:center;gap:7px}
  .brand-mark{width:22px;height:22px;background:var(--red)}
  .brand-name{font-family:"Open Sans",Arial,sans-serif;font-weight:700;font-size:19px;color:var(--ink)}
  .top-contact{position:absolute;right:41px;top:10px;display:flex;align-items:center;gap:12px;font-size:8px;color:var(--ink)}
  .top-email{display:flex;align-items:center;gap:4px}
  .top-phone{background:var(--red);color:#fff;font-weight:700;font-size:11px;padding:3px 9px;display:flex;align-items:center;gap:5px}

  .main-nav{position:absolute;left:272px;top:64px;width:368px;height:22px;background:var(--red);display:flex}
  .main-nav a{flex:auto;text-align:center;color:#fff;text-decoration:none;font-size:8px;font-weight:700;line-height:22px}
  .main-nav a.active{background:var(--ink)}

  /* hero */
  .hero{position:absolute;left:0;top:86px;width:681px;height:254px;
    background:linear-gradient(100deg,#6f7d6a 0%,#94a39b 30%,#b9c7d3 55%,#9fb6cc 75%,#c9c2b3 100%)}
  .hero-caption{position:absolute;left:300px;top:80px;width:168px;background:rgba(20,20,20,.6);color:#fff;padding:8px 10px}
  .hero-caption h1{font-size:10.5px;font-weight:700;line-height:1.3}
  .hero-caption p{font-size:9.5px;font-weight:700;line-height:1.3;margin-top:2px}
  .hero-rule{position:absolute;left:0;top:340px;width:681px;height:4px;background:var(--ink)}

  /* service cards */
  .cards{position:absolute;left:50px;top:364px;width:580px;display:flex;justify-content:space-between}
  .card{width:172px;height:190px;background:#fff;border-top:3px solid var(--red);box-shadow:0 2px 6px rgba(0,0,0,.18);padding:8px 9px}
  .card h2{font-family:"PT Serif",Georgia,serif;font-size:13px;color:var(--ink);font-weight:400;margin-bottom:6px}
  .card-photo{height:62px}
  .card p{font-size:6.8px;line-height:1.5;margin-top:7px}
  .read-more{display:block;text-align:right;color:var(--red);font-size:6.5px;font-weight:700;margin-top:5px}

  /* welcome + schedule */
  .welcome-band{position:absolute;left:0;top:580px;width:681px;height:250px;background:var(--band)}
  .welcome{position:absolute;left:50px;top:20px;width:390px}
  .welcome h2,.schedule h2{font-family:"PT Serif",Georgia,serif;font-size:14px;color:var(--ink);font-weight:700;margin-bottom:8px}
  .welcome p{font-size:7px;line-height:1.6;margin-bottom:8px}
  .schedule{position:absolute;left:462px;top:20px;width:168px}
  .field{height:15px;background:#fff;border:1px solid var(--line);font-size:6.5px;color:var(--muted);padding:3px 5px;margin-bottom:6px}
  .field-row{display:flex;gap:5px}
  .field-row .field{flex:1}
  .field.message{height:36px}
  .submit{display:inline-block;background:#9a9a9a;color:#fff;font-size:7px;font-weight:700;padding:3px 10px}

  /* features */
  .features{position:absolute;left:50px;top:846px;width:580px;display:flex;justify-content:space-between}
  .feature{width:174px}
  .feature h3{font-family:"PT Serif",Georgia,serif;font-size:12px;color:var(--ink);font-weight:700;margin-bottom:7px}
  .feature-photo{height:70px}
  .feature p{font-size:6.8px;line-height:1.5;margin-top:6px}
  .why-list{list-style:none}
  .why-list li{display:flex;align-items:center;gap:5px;font-size:7px;line-height:1;margin-bottom:8px}

  /* call to action */
  .cta{position:absolute;left:50px;top:1034px;width:580px;height:58px;background:var(--green);text-align:center;padding-top:9px}
  .cta h3{font-family:"PT Serif",Georgia,serif;font-size:12.5px;color:#fff;font-weight:700}
  .cta-form{display:flex;justify-content:center;gap:5px;margin-top:7px}
  .cta-input{width:110px;height:16px;background:#fff;font-size:6.5px;color:var(--muted);text-align:left;padding:4px 5px}
  .cta-button{background:var(--ink);color:#fff;font-size:6.5px;font-weight:700;padding:4px 9px}

  /* footer */
  .site-footer{position:absolute;left:0;top:1106px;width:681px;height:80px;background:var(--footer);color:var(--footer-text)}
  .footer-col{position:absolute;top:8px}
  .footer-col h4{font-size:8px;color:#fff;font-weight:600;margin-bottom:5px}
  .footer-col ul{list-style:none}
  .footer-col li{font-size:5.8px;line-height:1.55}
  .contact-line{display:flex;align-items:flex-start;gap:4px;font-size:5.8px;line-height:1.5;margin-bottom:4px}
  .footer-brand{position:absolute;right:40px;top:28px;display:flex;align-items:center;gap:6px;opacity:.45}
  .footer-brand .brand-mark{background:#777;width:18px;height:18px}
  .footer-brand .brand-name{color:#999;font-size:17px}
  .copyright{position:absolute;left:0;top:1186px;width:681px;height:14px;background:#0b0b0b;color:#777;font-size:6px;line-height:14px;padding-left:50px}
</style>
</head>
<body>

<header class="site-header">
  <div class="brand"><span class="brand-mark"></span><span class="brand-name">Tidy4All</span></div>
  <div class="top-contact">
    <span class="top-email">
      <svg width="10" height="7" viewBox="0 0 10 7"><rect x=".5" y=".5" width="9" height="6" fill="none" stroke="#e32421"/><path d="M.5 .5 5 4 9.5 .5" fill="none" stroke="#e32421"/></svg>
      info@tidy4all.com
    </span>
    <span class="top-phone">
      <svg width="9" height="9" viewBox="0 0 24 24"><path fill="#fff" d="M6.6 10.8a15.1 15.1 0 0 0 6.6 6.6l2.2-2.2a1 1 0 0 1 1-.25 11.4 11.4 0 0 0 3.6.57 1 1 0 0 1 1 1V20a1 1 0 0 1-1 1A17 17 0 0 1 3 4a1 1 0 0 1 1-1h3.5a1 1 0 0 1 1 1c0 1.25.2 2.45.57 3.57a1 1 0 0 1-.25 1z"/></svg>
      555 014 7890
    </span>
  </div>
</header>

<nav class="main-nav">
  <a class="active">Home</a><a>About Us</a><a>Services</a><a>Think Green</a><a>Customer Reviews</a><a>Contact Us</a>
</nav>

<section class="hero" role="img" aria-label="Green roll-off dumpster truck parked in front of a modern apartment building under a blue sky">
  <div class="hero-caption">
    <h1>We Are A full Service Cleaning Company</h1>
    <p>Specializing in commercial and apartment cleans</p>
  </div>
</section>
<div class="hero-rule"></div>

<section class="cards">
  <article class="card">
    <h2>Home Owner</h2>
    <div class="card-photo" role="img" aria-label="Dumpster filled with household debris" style="background:linear-gradient(135deg,#7a5a3a,#b08860,#5e4a36)"></div>
    <p>Move-out cleans, deep scrubs and debris haul-off for homeowners who want a spotless place without the heavy lifting or the hassle.</p>
    <span class="read-more">READ MORE &gt;</span>
  </article>
  <article class="card">
    <h2>Business Owner</h2>
    <div class="card-photo" role="img" aria-label="Orange commercial dumpster behind a business" style="background:linear-gradient(135deg,#c45a1c,#e08a3c,#8a4a24)"></div>
    <p>Reliable crews for offices, retail units and common areas, with photos and invoices sent after every job so you always know what was done.</p>
    <span class="read-more">READ MORE &gt;</span>
  </article>
  <article class="card">
    <h2>Rent-a-Dumpster</h2>
    <div class="card-photo" role="img" aria-label="Row of rental dumpsters at a construction site" style="background:linear-gradient(135deg,#8aa0b6,#c9cfd4,#6e7e5a)"></div>
    <p>Need room for a cleanout? Book a roll-off bin in the size you need and we deliver it on time, then haul it away.</p>
    <span class="read-more">READ MORE &gt;</span>
  </article>
</section>

<section class="welcome-band">
  <div class="welcome">
    <h2>Welcome To Tidy4All</h2>
    <p>Tidy4All is the cleaning branch of an established waste management company serving coastal Georgia. We focus on large commercial cleans and apartment turnovers for property managers, while keeping our rates fair for local family businesses.</p>
    <p>Every job is handled by a licensed and insured crew. When the work is done you receive dated digital photos and a clear invoice, so there is never a question about what was cleaned or what it cost.</p>
    <p>From a single unit to a full complex, we arrive with the equipment, the manpower and the dumpsters to finish fast and leave every space ready for the next tenant.</p>
    <span class="read-more">READ MORE &gt;</span>
  </div>
  <form class="schedule">
    <h2>Schedule A Service</h2>
    <div class="field">Name</div>
    <div class="field">Phone No</div>
    <div class="field-row"><div class="field">Day and Time</div><div class="field">Date</div></div>
    <div class="field">Email</div>
    <div class="field message">Message</div>
    <span class="submit">Submit</span>
  </form>
</section>

<section class="features">
  <div class="feature">
    <h3>24/7 Access</h3>
    <div class="feature-photo" role="img" aria-label="Sign reading 24 hour service" style="background:linear-gradient(135deg,#2e6fa8,#8fb6d8,#2a5a88)"></div>
    <p>Call or book online any hour of the day. Our team answers quickly and gets a crew or a bin to your site when you need it.</p>
  </div>
  <div class="feature">
    <h3>Reliable. Clean. Safe.</h3>
    <div class="feature-photo" role="img" aria-label="Row of clean green dumpsters" style="background:linear-gradient(180deg,#b9d4ea 0%,#b9d4ea 35%,#3f9a3a 36%,#2f7d2c 100%)"></div>
    <p>Clean, well kept containers and trained drivers who place every dumpster with care and leave your property just as they found it.</p>
  </div>
  <div class="feature">
    <h3>Why Choose Us</h3>
    <ul class="why-list">
      <li><svg width="8" height="8" viewBox="0 0 10 10"><path d="M1 5.5 4 8.5 9 1.5" fill="none" stroke="#e32421" stroke-width="2"/></svg>Wide selection of dumpster sizes available</li>
      <li><svg width="8" height="8" viewBox="0 0 10 10"><path d="M1 5.5 4 8.5 9 1.5" fill="none" stroke="#e32421" stroke-width="2"/></svg>Flexible, timely pickup and delivery</li>
      <li><svg width="8" height="8" viewBox="0 0 10 10"><path d="M1 5.5 4 8.5 9 1.5" fill="none" stroke="#e32421" stroke-width="2"/></svg>Fast service available</li>
      <li><svg width="8" height="8" viewBox="0 0 10 10"><path d="M1 5.5 4 8.5 9 1.5" fill="none" stroke="#e32421" stroke-width="2"/></svg>Easy online ordering and scheduling</li>
      <li><svg width="8" height="8" viewBox="0 0 10 10"><path d="M1 5.5 4 8.5 9 1.5" fill="none" stroke="#e32421" stroke-width="2"/></svg>Online account management</li>
      <li><svg width="8" height="8" viewBox="0 0 10 10"><path d="M1 5.5 4 8.5 9 1.5" fill="none" stroke="#e32421" stroke-width="2"/></svg>Instant online pricing</li>
    </ul>
  </div>
</section>

<section class="cta">
  <h3>Ready to get started? See what dumpsters are available in your area.</h3>
  <div class="cta-form"><span class="cta-input">Enter Your Zip Code</span><span class="cta-button">SHOW PRODUCTS</span></div>
</section>

<footer class="site-footer">
  <div class="footer-col" style="left:50px">
    <h4>Quick Links</h4>
    <ul><li>Home</li><li>About Us</li><li>Services</li><li>Think Green</li><li>Customer Reviews</li><li>Contact Us</li></ul>
  </div>
  <div class="footer-col" style="left:200px;width:130px">
    <h4>Contact Information</h4>
    <div class="contact-line"><svg width="7" height="9" viewBox="0 0 10 14"><path d="M5 0a5 5 0 0 0-5 5c0 4 5 9 5 9s5-5 5-9a5 5 0 0 0-5-5zm0 7a2 2 0 1 1 0-4 2 2 0 0 1 0 4z" fill="#e32421"/></svg><span>1200 Harbor Way, Suite 4,<br>Savannah, GA 31401</span></div>
    <div class="contact-line"><svg width="7" height="7" viewBox="0 0 24 24"><path fill="#e32421" d="M6.6 10.8a15.1 15.1 0 0 0 6.6 6.6l2.2-2.2a1 1 0 0 1 1-.25 11.4 11.4 0 0 0 3.6.57 1 1 0 0 1 1 1V20a1 1 0 0 1-1 1A17 17 0 0 1 3 4a1 1 0 0 1 1-1h3.5a1 1 0 0 1 1 1c0 1.25.2 2.45.57 3.57a1 1 0 0 1-.25 1z"/></svg><span>555 014 7890</span></div>
    <div class="contact-line"><svg width="8" height="6" viewBox="0 0 10 7"><rect x=".5" y=".5" width="9" height="6" fill="none" stroke="#e32421"/><path d="M.5 .5 5 4 9.5 .5" fill="none" stroke="#e32421"/></svg><span>info@tidy4all.com</span></div>
  </div>
  <div class="footer-col" style="left:360px">
    <h4>FAQ's</h4>
    <ul><li>What sizes of dumpsters do you offer?</li><li>How much does a dumpster cost?</li><li>How much debris can it hold?</li><li>How long can I keep the dumpster?</li><li style="color:#fff">More FAQs</li></ul>
  </div>
  <div class="footer-brand"><span class="brand-mark"></span><span class="brand-name">Tidy4All</span></div>
</footer>
<div class="copyright">© 2015 Tidy4All &nbsp;|&nbsp; All rights reserved</div>

</body>
</html>
```